Redesign of an existing homepage

This site needs a redesign
https://www.wanderhof-kelbach.de
This page with the accommodation options is important for the customer
https://www.wanderhof-kelbach.de/gastgeber/
Till now there is a new logo. See attachment. That's all I have.
It would make sense to use the colors of the logo in the redesign.
footer.jpg.
I would put this info into the footer. The graphic (Infomaterial) is not needed.
a new menu - links.jpg
This info can be put in a new menu. Therefore the right column is gone and there is more space for the design.
NEW:
Please keep in mind that the Icons are important and shall be displayed under every accommodation

```html
<!DOCTYPE html>
<html lang="en">
<head>
<meta charset="utf-8">
<title>Tourismusverband Kelbach – Holiday in the Kelbachtal</title>
<link href="https://fonts.googleapis.com/css2?family=Poppins:wght@400;500;600;700&display=swap" rel="stylesheet">
<style>
:root{
  --green:#7cc142;
  --green-dark:#5fa52b;
  --blue:#1e9bd7;
  --blue-dark:#1580b8;
  --ink:#222831;
  --text:#5b6169;
  --muted:#9aa0a6;
  --line:#e6e8eb;
  --white:#ffffff;
  --footer-bar:#1d6f9e;
}
*{box-sizing:border-box;margin:0;padding:0}
html,body{width:1200px;height:3472px;overflow:hidden;background:var(--white)}
body{position:relative;font-family:"Poppins",sans-serif;color:var(--text)}
.abs{position:absolute}

/* header */
.site-header{left:0;top:0;width:1200px;height:96px;background:var(--white);z-index:5}
.brand{left:40px;top:20px;display:flex;align-items:center;gap:10px}
.brand-dot{width:34px;height:34px;border-radius:50%;background:var(--green)}
.brand-name{font-weight:700;font-size:13px;line-height:15px;color:var(--green-dark);letter-spacing:.3px;width:150px}
.partners{left:470px;top:10px;display:flex;gap:22px}
.partner-badge{width:64px;height:30px;border-radius:4px;background:#e9eef2}
.partner-badge:nth-child(2){background:#dcecf6}
.partner-badge:nth-child(3){background:#e6f2dc}
.partner-badge:nth-child(4){background:#eef0f3}
.phone-pill{left:930px;top:10px;height:34px;padding:0 18px;border-radius:17px;background:var(--green);color:var(--white);font-size:14px;font-weight:600;display:flex;align-items:center;gap:8px}
.main-nav{left:400px;top:62px;display:flex;gap:30px;font-size:13px;font-weight:500;color:var(--ink)}
.main-nav a{color:inherit;text-decoration:none;padding-bottom:6px}
.main-nav a.active{color:var(--green-dark);border-bottom:2px solid var(--green)}

/* hero */
.hero{left:0;top:96px;width:1200px;height:520px;overflow:hidden}
.hero-photo{position:absolute;inset:0;background:linear-gradient(100deg,#3c4a2a 0%,#6f7a45 35%,#c9b27c 60%,#e7d7b0 78%,#8fa56a 100%)}
.hero-shade{position:absolute;inset:0;background:linear-gradient(90deg,rgba(0,0,0,.55) 0%,rgba(0,0,0,.25) 45%,rgba(0,0,0,0) 70%)}
.hero-curve{position:absolute;left:0;bottom:0;width:1200px;height:80px}
.hero-text{left:150px;top:180px;color:var(--white);z-index:2}
.hero-kicker{font-size:12px;font-weight:600;letter-spacing:.6px}
.hero-title{font-size:40px;font-weight:700;line-height:48px;margin-top:10px;width:470px}
.hero-sub{font-size:14px;line-height:20px;margin-top:16px;width:330px}
.btn{display:inline-flex;align-items:center;justify-content:center;height:36px;padding:0 22px;border-radius:18px;font-size:12px;font-weight:600;letter-spacing:.5px;text-decoration:none}
.btn-green{background:var(--green);color:var(--white)}
.btn-outline{border:2px solid var(--white);color:var(--white)}
.hero-text .btn{margin-top:26px}
.slider-dots{display:flex;gap:8px}
.slider-dots span{width:7px;height:7px;border-radius:50%;background:#c9cdd1}
.slider-dots span.on{background:var(--blue)}
.hero-dots{left:570px;top:566px;z-index:3}
.hero-dots span{background:rgba(255,255,255,.6)}
.hero-dots span.on{background:var(--white)}
.brand-seal{left:860px;top:340px;width:250px;height:250px;border-radius:50%;background:var(--white);box-shadow:0 8px 24px rgba(0,0,0,.15);z-index:4;display:flex;align-items:center;justify-content:center;text-align:center}
.brand-seal span{font-weight:700;font-size:18px;line-height:24px;color:var(--green-dark);width:170px}

/* intro */
.intro{left:0;top:800px;width:1200px;text-align:center}
.intro h2{font-size:28px;font-weight:700;line-height:38px;color:var(--ink);width:760px;margin:0 auto}
.intro-sub{font-size:16px;font-weight:600;color:var(--ink);margin-top:14px}
.intro p{font-size:12px;line-height:20px;width:880px;margin:16px auto 0;color:var(--text)}
.intro .btn{margin-top:36px}

/* hosts */
.section-title{font-size:28px;font-weight:700;color:var(--ink)}
.hosts-title{left:140px;top:1226px}
.arrows{display:flex;gap:12px}
.arrow{width:32px;height:32px;border-radius:50%;display:flex;align-items:center;justify-content:center}
.arrow.light{background:var(--white);color:var(--ink)}
.arrow.blue{background:var(--blue);color:var(--white)}
.hosts-arrows{left:960px;top:1232px}
.host-card{top:1320px;width:268px;height:424px;background:var(--white);box-shadow:0 4px 18px rgba(0,0,0,.1);border-radius:4px;overflow:hidden}
.host-card.faded{opacity:.35}
.host-photo{height:232px}
.host-body{padding:18px 18px}
.host-price{font-size:18px;font-weight:700;color:var(--green-dark)}
.host-name{font-size:16px;font-weight:600;color:var(--ink);margin-top:6px}
.host-desc{font-size:11px;line-height:17px;margin-top:8px;color:var(--text)}
.host-more{display:flex;justify-content:space-between;align-items:center;margin-top:16px;font-size:11px;font-weight:600;color:var(--green-dark)}
.host-amenities{display:flex;gap:6px}
.host-amenities i{width:14px;height:14px;border-radius:3px;background:var(--line);display:block}
.hosts-dots{left:578px;top:1770px}

/* leisure */
.leisure-band{left:0;top:1800px;width:1200px;height:640px}
.leisure-head{left:0;top:1900px;width:1200px;text-align:center;color:var(--white)}
.leisure-head h2{font-size:28px;font-weight:700}
.leisure-head p{font-size:14px;margin-top:8px}
.activity-row{left:150px;top:2030px;display:flex;gap:40px}
.activity-card{width:195px;height:230px;background:var(--white);border-radius:6px;text-align:center;padding:22px 16px;box-shadow:0 6px 18px rgba(0,0,0,.12)}
.activity-icon{width:60px;height:60px;border-radius:50%;background:var(--green);margin:0 auto}
.activity-card h3{font-size:16px;font-weight:600;color:var(--ink);margin-top:14px}
.activity-card p{font-size:11px;line-height:17px;margin-top:8px}
.leisure-prev{left:90px;top:2128px}
.leisure-next{left:1078px;top:2128px}
.leisure-cta{left:0;top:2320px;width:1200px;text-align:center}

/* video */
.video-title{left:0;top:2500px;width:1200px;text-align:center}
.video-frame{left:140px;top:2580px;width:920px;height:400px;border-radius:4px;overflow:hidden;background:linear-gradient(160deg,#8fb7d8 0%,#b9ccd8 35%,#a6866a 62%,#6b5a4b 100%)}
.play-btn{left:570px;top:2750px;width:60px;height:60px;border-radius:50%;background:var(--green);display:flex;align-items:center;justify-content:center;box-shadow:0 4px 14px rgba(0,0,0,.25)}

/* footer */
.site-footer{left:0;top:3010px;width:1200px;height:462px;color:var(--white)}
.footer-bg{position:absolute;inset:0;width:1200px;height:462px}
.footer-col{top:3120px;color:var(--white)}
.footer-col h4{font-size:14px;font-weight:700;letter-spacing:.5px;margin-bottom:12px}
.footer-col ul{list-style:none;font-size:12px;line-height:22px}
.footer-col li{display:flex;align-items:center;gap:8px}
.footer-col li::before{content:"";width:6px;height:6px;border-radius:50%;background:var(--white);opacity:.8}
.footer-col.contact li::before{display:none}
.contact-icon{width:18px;height:18px;border-radius:50%;background:rgba(255,255,255,.25);display:flex;align-items:center;justify-content:center;flex:none}
.map-box{width:250px;height:150px;border-radius:4px;background:linear-gradient(135deg,#e8efe6,#cfe1ef)}
.copyright{left:0;top:3418px;width:1200px;height:54px;background:var(--footer-bar);font-size:12px;display:flex;align-items:center;justify-content:center;color:var(--white)}
</style>
</head>
<body>

<header class="site-header abs">
  <div class="brand abs"><span class="brand-dot"></span><span class="brand-name">TOURISMUSVERBAND KELBACH</span></div>
  <div class="partners abs"><span class="partner-badge"></span><span class="partner-badge"></span><span class="partner-badge"></span><span class="partner-badge"></span></div>
  <div class="phone-pill abs">
    <svg width="14" height="14" viewBox="0 0 24 24" fill="#fff"><path d="M6.6 10.8a15 15 0 006.6 6.6l2.2-2.2a1 1 0 011-.25 11.4 11.4 0 003.6.57 1 1 0 011 1V20a1 1 0 01-1 1A17 17 0 013 4a1 1 0 011-1h3.5a1 1 0 011 1c0 1.25.2 2.45.57 3.6a1 1 0 01-.25 1z"/></svg>
    08000 / 123 45 67
  </div>
  <nav class="main-nav abs">
    <a class="active" href="#">Home</a><a href="#">Host</a><a href="#">Kelbachtal</a><a href="#">Leisure Time</a><a href="#">Excursion Destinations</a><a href="#">Art &amp; Culture</a><a href="#">Contact</a>
  </nav>
</header>

<section class="hero abs">
  <div class="hero-photo" role="img" aria-label="Photo of a smiling couple exploring the sunny Bavarian countryside"></div>
  <div class="hero-shade"></div>
  <svg class="hero-curve" viewBox="0 0 1200 80" preserveAspectRatio="none"><path d="M0 80 L0 60 Q600 0 1200 30 L1200 80 Z" fill="#fff"/></svg>
</section>
<div class="hero-text abs">
  <div class="hero-kicker">WELCOME TO TOURISMUSVERBAND KELBACH</div>
  <h1 class="hero-title">Holiday In The Kelbachtal The Most Beautiful Spot In Bavaria</h1>
  <p class="hero-sub">Enjoy Our Hospitality. A Visit Is Worthwhile at any Time of Year, We look forward to seeing you!</p>
  <a class="btn btn-green" href="#">GET STARTED</a>
</div>
<div class="slider-dots hero-dots abs"><span class="on"></span><span></span><span></span><span></span></div>
<div class="brand-seal abs"><span>Tourismusverband Kelbach</span></div>

<section class="intro abs">
  <h2>Kelbach &amp; The Surrounding Area Have Everything That Makes Life Worth Living:</h2>
  <div class="intro-sub">Culture &amp; Nature, Joie De Vivre &amp; Enjoyment, Friendly &amp; Open-minded People</div>
  <p>Whether churches, fountains or other architectural monuments – on a tour through the town you can discover many lovely details for yourself. For those who enjoy exercise and close contact with nature, the gentle hills offer cycling, walking, hiking, golfing, horseback riding and swimming, or simply enjoy the peace and quiet.</p>
  <p>Leisure and relaxation for the whole family – spend a holiday on a farm, in a holiday apartment or in a hotel. Your vacation in the Kelbachtal will be a unique experience!</p>
  <a class="btn btn-green" href="#">READ MORE</a>
</section>

<h2 class="section-title hosts-title abs">Host In The Kelbachtal</h2>
<div class="arrows hosts-arrows abs">
  <span class="arrow light"><svg width="10" height="10" viewBox="0 0 10 10"><path d="M7 1 3 5l4 4" stroke="#222831" stroke-width="1.6" fill="none"/></svg></span>
  <span class="arrow blue"><svg width="10" height="10" viewBox="0 0 10 10"><path d="M3 1l4 4-4 4" stroke="#fff" stroke-width="1.6" fill="none"/></svg></span>
</div>

<article class="host-card faded abs" style="left:-150px">
  <div class="host-photo" role="img" aria-label="Photo of a guesthouse" style="background:linear-gradient(160deg,#bcd3e6,#8a7a5e)"></div>
  <div class="host-body"><div class="host-price">€72,00</div><div class="host-name">Landhaus Ebner</div><div class="host-desc">Quiet rooms near the woods with breakfast served daily.</div><div class="host-more">MORE DETAILS</div></div>
</article>
<article class="host-card abs" style="left:140px">
  <div class="host-photo" role="img" aria-label="Photo of a lakeside hotel building" style="background:linear-gradient(160deg,#a9c6de,#8c6a4e 70%,#5e4a38)"></div>
  <div class="host-body"><div class="host-price">€86,00</div><div class="host-name">Seehotel Lindenau</div><div class="host-desc">A star in the bay heaven. Accommodation and pampering with a lake view.</div><div class="host-more">MORE DETAILS<span class="host-amenities"><i></i><i></i><i></i></span></div></div>
</article>
<article class="host-card abs" style="left:440px">
  <div class="host-photo" role="img" aria-label="Photo of a traditional farmhouse inn" style="background:linear-gradient(160deg,#b4cfe4,#c9b89a 55%,#6f7e4d)"></div>
  <div class="host-body"><div class="host-price">€48,00</div><div class="host-name">Brunnerhof</div><div class="host-desc">We offer peace, relaxation and hospitality in well furnished holiday apartments.</div><div class="host-more">MORE DETAILS<span class="host-amenities"><i></i><i></i><i></i></span></div></div>
</article>
<article class="host-card abs" style="left:740px">
  <div class="host-photo" role="img" aria-label="Photo of a farm holiday house with balconies" style="background:linear-gradient(160deg,#a6c4de,#d9cdb5 50%,#7d8c55)"></div>
  <div class="host-body"><div class="host-price">€100,00</div><div class="host-name">Ferienhof Wagner</div><div class="host-desc">Farm holiday home, holiday apartments, campsite. Our quality is our pride.</div><div class="host-more">MORE DETAILS<span class="host-amenities"><i></i><i></i><i></i></span></div></div>
</article>
<article class="host-card faded abs" style="left:1040px">
  <div class="host-photo" role="img" aria-label="Photo of a holiday apartment house" style="background:linear-gradient(160deg,#c2d6e8,#9c8b70)"></div>
  <div class="host-body"><div class="host-price">€64,00</div><div class="host-name">Haus Sonne</div><div class="host-desc">Holiday apartments for families.</div><div class="host-more">MORE DETAILS</div></div>
</article>
<div class="slider-dots hosts-dots abs"><span class="on"></span><span></span><span></span><span></span></div>

<svg class="leisure-band abs" viewBox="0 0 1200 640" preserveAspectRatio="none">
  <path d="M0 40 Q300 -10 650 40 T1200 20 L1200 600 Q800 660 400 600 T0 610 Z" fill="#7cc142"/>
  <path d="M0 60 Q320 10 660 60 T1200 45 L1200 585 Q820 640 420 585 T0 595 Z" fill="#1e9bd7"/>
</svg>
<div class="leisure-head abs">
  <h2>Leisure &amp; Relaxation For The Whole Family</h2>
  <p>Enjoy Peace and Relaxation In Nature Combined With Select Activities</p>
</div>
<span class="arrow light leisure-prev abs"><svg width="10" height="10" viewBox="0 0 10 10"><path d="M7 1 3 5l4 4" stroke="#222831" stroke-width="1.6" fill="none"/></svg></span>
<div class="activity-row abs">
  <div class="activity-card"><div class="activity-icon"></div><h3>Fishing</h3><p>Around the approximately 60 hectare lake in Kelbach, you'll find</p></div>
  <div class="activity-card"><div class="activity-icon"></div><h3>Balloon Rides</h3><p>Around the approximately 60 hectare lake in Kelbach, you'll find</p></div>
  <div class="activity-card"><div class="activity-icon"></div><h3>Outdoor Pools</h3><p>Around the approximately 60 hectare lake in Kelbach, you'll find</p></div>
  <div class="activity-card"><div class="activity-icon"></div><h3>Golf</h3><p>Around the approximately 60 hectare lake in Kelbach, you'll find</p></div>
</div>
<span class="arrow light leisure-next abs"><svg width="10" height="10" viewBox="0 0 10 10"><path d="M3 1l4 4-4 4" stroke="#222831" stroke-width="1.6" fill="none"/></svg></span>
<div class="leisure-cta abs"><a class="btn btn-outline" href="#">LEARN MORE</a></div>

<h2 class="section-title video-title abs">Watch Video</h2>
<div class="video-frame abs" role="img" aria-label="Video still of the town square with a horse statue and historic buildings"></div>
<div class="play-btn abs"><svg width="20" height="22" viewBox="0 0 20 22"><path d="M3 2l15 9-15 9z" fill="#fff"/></svg></div>

<footer class="site-footer abs">
  <svg class="footer-bg" viewBox="0 0 1200 462" preserveAspectRatio="none">
    <defs><linearGradient id="footerGrad" x1="0" y1="0" x2="1" y2="1"><stop offset="0" stop-color="#7cc142"/><stop offset=".55" stop-color="#2aa6c9"/><stop offset="1" stop-color="#1e9bd7"/></linearGradient></defs>
    <path d="M0 40 Q350 0 700 35 T1200 25 L1200 462 L0 462 Z" fill="url(#footerGrad)"/>
  </svg>
</footer>
<div class="footer-col abs" style="left:140px">
  <h4>LINKS</h4>
  <ul><li>Informationen</li><li>Impressum</li><li>Datenschutz</li></ul>
  <h4 style="margin-top:26px">FOLLOW US</h4>
  <ul><li>Photo Feed</li><li>Business Network</li><li>Community Page</li></ul>
</div>
<div class="footer-col contact abs" style="left:400px">
  <h4>CONTACT DETAILS</h4>
  <ul>
    <li><span class="contact-icon"><svg width="10" height="10" viewBox="0 0 24 24" fill="#fff"><path d="M6.6 10.8a15 15 0 006.6 6.6l2.2-2.2a1 1 0 011-.25 11.4 11.4 0 003.6.57 1 1 0 011 1V20a1 1 0 01-1 1A17 17 0 013 4a1 1 0 011-1h3.5a1 1 0 011 1c0 1.25.2 2.45.57 3.6a1 1 0 01-.25 1z"/></svg></span>08000 / 123 45 67</li>
    <li style="margin-top:6px"><span class="contact-icon"><svg width="10" height="10" viewBox="0 0 24 24"><rect x="3" y="6" width="18" height="12" fill="none" stroke="#fff" stroke-width="2"/><path d="M3 6l9 7 9-7" fill="none" stroke="#fff" stroke-width="2"/></svg></span>info@wanderhof-kelbach.de</li>
    <li style="margin-top:6px"><span class="contact-icon"><svg width="10" height="10" viewBox="0 0 24 24" fill="#fff"><path d="M12 2a7 7 0 00-7 7c0 5 7 13 7 13s7-8 7-13a7 7 0 00-7-7zm0 9.5A2.5 2.5 0 1112 6.5a2.5 2.5 0 010 5z"/></svg></span>Marktplatz 4, 94999 Kelbach</li>
    <li style="margin-top:6px;align-items:flex-start"><span class="contact-icon"><svg width="10" height="10" viewBox="0 0 24 24"><circle cx="12" cy="12" r="9" fill="none" stroke="#fff" stroke-width="2"/><path d="M12 7v5l3 2" fill="none" stroke="#fff" stroke-width="2"/></svg></span><span>Mon-Thurs: 8:00 - 16:00<br>Fri: 8:00 - 12:00</span></li>
  </ul>
</div>
<div class="footer-col contact abs" style="left:810px">
  <h4>HOW TO REACH US</h4>
  <div class="map-box" role="img" aria-label="Map showing the location of the tourist office in Kelbach"></div>
</div>
<div class="copyright abs">© 2022 Copyright All Right Reserved. Tourismusverband Kelbach</div>

</body>
</html>
```